Small environmental consultancy needs a simple but professional web design

We are a boutique environmental consultancyand contracting business located in Margaret River in the South West of Western Australia.

We have two arms
1) Consulting which offers environmental planning, management and assessment services primarily to local government and the development industry.
2) Contracting which implements on site plans and on ground works primarily involving revegetation, bush regeneration and environmental weed control.

We need a simple yet professional web design within the wordpress platform that commmunicates professionalism, experience and technical expertise without appearing too corporate.

Something like this structure appeals:
http://fernquill.net.au/environment-services/
or
http://www.tallowbrookenvironmental.com.au/index.php

(without the image gallery function)

Target Market(s)

Local Government Officers deciding on tenders;
Developers, Engineers, Town Planning consultants looking for environmental expertise

Industry/Entity Type

Business

Number of Pages Required

5+ page

Font styles to use
Sans Serif

Colors
33a6d7
9bcb3c

Requirements
Must have
• Pages required include:
• Home
• Environmental Planning and Management
• Revegetation and Regeneration Implementation (This page can mirror the Environmental Planning and Management page exactly in structure but with different text and images)
• About Us (I think that this page can be relatively simple and generic)
• Contact (I think that this page can be very simple and generic)
Nice to have
• An ability to start out basic and quicikly establish a website presence and then build in additional drop downs and pages over time.
Should not have
• It does not need a photo gallery page;
• It does not need a major amount of space dedicated to social media and blogs etc as this is not currently particularly active area for us

```html
<!DOCTYPE html>
<html lang="en">
<head>
<meta charset="utf-8">
<title>Wattlebird Ecoservices – Revegetation and Bush Regeneration</title>
<link rel="stylesheet" href="https://fonts.googleapis.com/css2?family=Open+Sans:wght@400;600;700&family=Raleway:wght@700&family=Teko:wght@400;500&display=swap">
<style>
:root{
  --blue:#33a6d7;
  --blue-dark:#2a8cc2;
  --green:#9bcb3c;
  --green-dark:#7d9f1f;
  --brown:#6b4a1c;
  --text:#555555;
  --heading:#333333;
  --header-bg:#efefef;
  --footer-bg:#ebebeb;
  --line:#d6d6d6;
  --field:#ffffff;
  --placeholder:#a8a8a8;
  --icon:#b5b5b5;
}
*{box-sizing:border-box;margin:0;padding:0}
html,body{width:1064px;height:1200px;overflow:hidden}
body{position:relative;background:#fff;font-family:"Open Sans",Arial,sans-serif;color:var(--text)}
.abs{position:absolute}

/* header */
.site-header{left:0;top:0;width:1064px;height:155px;background:linear-gradient(180deg,#f4f4f4,var(--header-bg))}
.brand{left:72px;top:46px;display:flex;align-items:center;gap:16px}
.brand-dot{width:54px;height:54px;border-radius:50%;background:var(--green)}
.brand-name{font-size:33px;font-weight:400;color:var(--brown);line-height:1}
.brand-tagline{left:142px;top:88px;font-size:12.5px;color:var(--brown);font-weight:600}
.call-label{left:849px;top:34px;font-size:15.5px;font-weight:700;color:#222}
.call-number{left:849px;top:50px;font-size:25px;font-weight:700;color:var(--blue)}
.search{left:810px;top:93px;width:188px;height:25px;background:#fff;border:1px solid #e3e3e3;font-size:12px;color:#444;padding:4px 9px}
.search svg{position:absolute;right:6px;top:5px}

/* navigation */
.main-nav{left:0;top:155px;width:1064px;height:39px;background:var(--blue);border-bottom:2px solid var(--blue-dark)}
.nav-item{top:0;height:37px;line-height:37px;font-family:"Raleway",sans-serif;font-weight:700;font-size:11.4px;color:#fff;text-transform:uppercase;white-space:nowrap}
.nav-item.is-active{background:var(--blue-dark);width:279px;text-align:center}

/* banner */
.banner{left:0;top:195px;width:1064px;height:112px;background:linear-gradient(90deg,#5b4a33 0%,#8c7a52 25%,#a9b6a4 50%,#c9d6cf 62%,#6d6a55 80%,#3f3a2c 100%)}

/* content */
.page-title{left:65px;top:342px;font-family:"Teko",sans-serif;font-weight:500;font-size:33px;color:var(--green);text-transform:uppercase;letter-spacing:-.8px;line-height:1.2;white-space:nowrap}
.copy p{font-size:11.6px;line-height:18.7px;color:var(--text)}
.copy-narrow{left:65px;top:395px;width:536px}
.copy-narrow p+p{margin-top:18px}
.copy-wide{left:65px;top:694px;width:934px}
.copy-wide p+p{margin-top:18px}
.feature-image{left:625px;top:399px;width:373px;height:253px;background:radial-gradient(circle at 50% 35%,#f5fbd8 0%,#c9e27c 40%,#8fbf3a 100%)}

/* footer */
.site-footer{left:0;top:910px;width:1064px;height:290px;background:var(--footer-bg);border-top:1px solid var(--line)}
.footer-heading{font-family:"Teko",sans-serif;font-size:21px;font-weight:400;color:var(--heading);text-transform:uppercase;line-height:1}
.footer-links{font-size:12px;line-height:18px;color:#444}
.call-now{left:64px;top:1050px}
.call-now-number{left:65px;top:1074px;display:flex;align-items:center;gap:8px;font-family:"Teko",sans-serif;font-size:29px;color:var(--green);line-height:1}
.field{background:var(--field);border:1px solid #dcdcdc;font-size:13px;color:var(--placeholder);padding:7px 12px}
.field svg{position:absolute}
.send-button{left:545px;top:1091px;width:138px;height:39px;background:linear-gradient(180deg,#9bbf2f,var(--green-dark));border:1px solid #6d8c17;font-family:"Teko",sans-serif;font-size:20px;color:#fff;text-align:center;line-height:40px;text-transform:uppercase}
.footer-rule{left:65px;top:1156px;width:956px;height:1px;background:var(--line)}
.copyright{left:65px;top:1171px;font-size:12px;color:#444}
</style>
</head>
<body>

<header class="abs site-header">
  <div class="abs brand"><span class="brand-dot"></span><span class="brand-name">Wattlebird Ecoservices</span></div>
  <div class="abs brand-tagline">Environmental Assessment, Planning &amp; Management</div>
  <div class="abs call-label">Call Us</div>
  <div class="abs call-number">0412 738 064</div>
  <div class="abs search">Search
    <svg width="14" height="14" viewBox="0 0 14 14"><circle cx="6" cy="6" r="4.5" fill="none" stroke="#999" stroke-width="1.6"/><line x1="9.3" y1="9.3" x2="13" y2="13" stroke="#999" stroke-width="1.8"/></svg>
  </div>
</header>

<nav class="abs main-nav">
  <span class="abs nav-item" style="left:90px">Home</span>
  <span class="abs nav-item" style="left:162px">Environmental Planning and Management</span>
  <span class="abs nav-item is-active" style="left:453px">Revegetation and Bush Regeneration</span>
  <span class="abs nav-item" style="left:751px">About Us</span>
  <span class="abs nav-item" style="left:848px">Contact</span>
</nav>

<div class="abs banner" role="img" aria-label="Sunlit forest with tall tree trunks"></div>

<main>
  <h1 class="abs page-title">Revegetation and Bush Regeneration</h1>
  <div class="abs copy copy-narrow">
    <p>Lorem ipsum dolor sit amet, consectetuer adipiscing elit, sed diam nonummy nibh euismod tincidunt ut laoreet dolore magna aliquam erat ullamcorper suscipit lobortis nisl ut aliquip ex ea commodo consequat. Lorem ipsum dolor sit amet, consectetuer adipiscing elit, sed diam nonummy nibh euismod tincidunt ut laoreet dolore magna aliquam erat volutpat. Ut wisi enim ad minim veniam, quis nostrud exerci tation ullamcorper suscipit lobortis nisl ut aliquip ex ea commodo consequat.Lorem ipsum dolor sit amet, consectetuer adipiscing elit, sed diam nonummy nibh euismod tincidunt ut laoreet dolore magna aliquam erat volutpat. Ut wisi enim ad minim veniam, quis nostrud exerci tation ullamcorper suscipit lobortis nisl ut aliquip ex ea commodo consequat.</p>
    <p>Lorem ipsum dolor sit amet, consectetuer adipiscing elit, sed diam nonummy nibh euismod tincidunt ut laoreet dolore magna aliquam erat volutpat. Ut wisi enim ad minim veniam, quis nostrud exerci tation ullamcorper suscipit lobortis nisl ut aliquip ex ea commodo consequat. Lorem ipsum dolor sit amet, consectetuer adipiscing elit, sed diam nonummy nibh euismod tincidunt ut laoreet dolore magna aliquam erat ullamcorper suscipit lobortis nisl ut aliquip ex ea commodo consequat.</p>
  </div>
  <div class="abs feature-image" role="img" aria-label="Cupped hands holding soil with a young green seedling"></div>
  <div class="abs copy copy-wide">
    <p>Lorem ipsum dolor sit amet, consectetuer adipiscing elit, sed diam nonummy nibh euismod tincidunt ut laoreet dolore magna aliquam erat ullamcorper suscipit lobortis nisl ut aliquip ex ea commodo consequat. Lorem ipsum dolor sit amet, consectetuer adipiscing elit, sed diam nonummy nibh euismod tincidunt ut laoreet dolore magna aliquam erat volutpat. Ut wisi enim ad minim veniam, quis nostrud exerci tation ullamcorper suscipit lobortis nisl ut aliquip ex ea commodo consequat.Lorem ipsum dolor sit amet, consectetuer adipiscing elit, sed diam nonummy nibh euismod tincidunt ut laoreet dolore magna aliquam erat volutpat. Ut wisi enim ad minim veniam, quis nostrud exerci tation ullamcorper suscipit lobortis nisl ut aliquip ex ea commodo consequat.</p>
    <p>Lorem ipsum dolor sit amet, consectetuer adipiscing elit, sed diam nonummy nibh euismod tincidunt ut laoreet dolore magna aliquam erat volutpat. Ut wisi enim ad minim veniam, quis nostrud exerci tation ullamcorper suscipit lobortis nisl ut aliquip ex ea commodo consequat. Lorem ipsum dolor sit amet, consectetuer adipiscing elit, sed diam nonummy nibh euismod tincidunt ut laoreet dolore magna aliquam erat ullamcorper suscipit lobortis nisl ut aliquip ex ea commodo consequat.</p>
  </div>
</main>

<footer class="abs site-footer"></footer>
<h2 class="abs footer-heading" style="left:65px;top:940px">About</h2>
<div class="abs footer-links" style="left:65px;top:966px">Environmental Planning and Management<br>Revegetation and Bush Regeneration<br>Contacts</div>
<h2 class="abs footer-heading" style="left:334px;top:940px">Website</h2>
<div class="abs footer-links" style="left:334px;top:966px">www.wattlebirdecoservices.com.au</div>
<h2 class="abs footer-heading call-now">Call us now:</h2>
<div class="abs call-now-number">
  <svg width="20" height="20" viewBox="0 0 20 20"><path d="M4 2l4 1 1 4-2 2c1 2.5 3 4.5 5 5l2-2 4 1 1 4-2 2C9 19 1 11 2 4z" fill="#444"/></svg>
  <span>0412 738 064</span>
</div>
<h2 class="abs footer-heading" style="left:545px;top:940px">Contact us</h2>
<div class="abs field" style="left:545px;top:977px;width:222px;height:32px">Name
  <svg style="right:7px;top:6px" width="18" height="18" viewBox="0 0 18 18"><circle cx="9" cy="5" r="4" fill="var(--icon)"/><path d="M1 18c0-5 3.5-7.5 8-7.5s8 2.5 8 7.5z" fill="var(--icon)"/></svg>
</div>
<div class="abs field" style="left:775px;top:977px;width:223px;height:32px">E-mail
  <svg style="right:7px;top:8px" width="20" height="15" viewBox="0 0 20 15"><rect width="20" height="15" rx="1" fill="var(--icon)"/><path d="M0 1l10 7 10-7" fill="none" stroke="#fff" stroke-width="1.5"/></svg>
</div>
<div class="abs field" style="left:545px;top:1018px;width:453px;height:65px">Message
  <svg style="right:8px;top:6px" width="20" height="17" viewBox="0 0 20 17"><path d="M1 1h18v11H7l-4 4v-4H1z" fill="var(--icon)"/><circle cx="6" cy="6.5" r="1.2" fill="#fff"/><circle cx="10" cy="6.5" r="1.2" fill="#fff"/><circle cx="14" cy="6.5" r="1.2" fill="#fff"/></svg>
</div>
<div class="abs send-button">Send message</div>
<div class="abs footer-rule"></div>
<div class="abs copyright">© 2015 Wattlebird Ecoservices. All Rights Reserved.</div>

</body>
</html>
```